Business Card Design

Online clothing womens clothing store, I sell my clothing online and at the markets.

i would like the attached picture on the front of the card and the contact information on the back.

Industry/Entity Type

Business

Contact Information for Business Card

Marlow Thread
Karen Whitfield
(Instagram symbol) _marlow_thread_
(Facebook symbol) www.fakebookexample.com/marlowthreadau/

W : www.marlowthread.example.au
E : info@marlowthread.example.au
P : 0498716204

```html
<!DOCTYPE html>
<html lang="en">
<head>
<meta charset="utf-8">
<title>Marlow Thread – Business Card</title>
<link rel="stylesheet" href="https://fonts.googleapis.com/css2?family=Open+Sans:wght@400;600;700&display=swap">
<style>
  :root {
    --backdrop: #d9d9d9;
    --ink: #000000;
    --panel: #161616;
    --paper: #ffffff;
    --rule: #e8e8e8;
    --photo-light: #dfe1e2;
    --photo-mid: #a9b0b4;
    --photo-dark: #4a4e52;
  }
  html, body {
    margin: 0;
    width: 1200px;
    height: 900px;
    overflow: hidden;
    background: var(--backdrop);
    font-family: "Open Sans", Arial, sans-serif;
  }
  .sheet {
    position: relative;
    width: 1200px;
    height: 900px;
  }
  .card {
    position: absolute;
    left: 260px;
    width: 680px;
    height: 388px;
    overflow: hidden;
    box-shadow: 0 6px 18px rgba(0,0,0,.18);
  }
  /* front */
  .card--front { top: 50px; background: var(--paper); }
  .front-photo {
    position: absolute;
    inset: 0 0 auto 0;
    height: 330px;
    background:
      radial-gradient(ellipse 38% 60% at 78% 55%, var(--photo-dark) 0%, rgba(74,78,82,.55) 45%, rgba(74,78,82,0) 75%),
      linear-gradient(180deg, var(--photo-light) 0%, var(--photo-mid) 100%);
  }
  .front-brand {
    position: absolute;
    left: 36px;
    top: 248px;
    margin: 0;
    font-weight: 600;
    font-size: 50px;
    letter-spacing: 4px;
    text-transform: uppercase;
    color: var(--paper);
    line-height: 1;
  }
  .front-strip { position: absolute; left: 0; right: 0; top: 330px; height: 10px; background: var(--paper); }
  .front-band  { position: absolute; left: 0; right: 0; top: 340px; height: 38px; background: var(--ink); }

  /* back */
  .card--back { top: 468px; background: var(--ink); color: var(--paper); }
  .back-name {
    position: absolute;
    left: 0; right: 0;
    top: 96px;
    margin: 0;
    text-align: center;
    font-weight: 700;
    font-size: 26px;
    line-height: 1.2;
  }
  .back-panel {
    position: absolute;
    left: 0; right: 0;
    top: 170px;
    height: 150px;
    background: var(--panel);
  }
  .contact {
    position: absolute;
    margin: 0;
    display: flex;
    align-items: center;
    gap: 12px;
    font-size: 15px;
    line-height: 18px;
  }
  .contact svg { width: 14px; height: 14px; flex: none; }
  .contact--web    { left: 26px; top: 14px; }
  .contact--handle { left: 26px; top: 38px; }
  .contact--phone  { right: 30px; top: 90px; }
  .contact--email  { right: 30px; top: 116px; }
  .panel-rule { position: absolute; left: 0; width: 400px; top: 66px; height: 5px; background: var(--rule); }
  .panel-cut  { position: absolute; left: 0; width: 400px; top: 71px; height: 79px; background: var(--ink); }
  .back-social {
    position: absolute;
    left: 0; right: 0;
    top: 328px;
    margin: 0;
    text-align: center;
    font-size: 16px;
    line-height: 20px;
  }
  .back-rule { position: absolute; left: 0; right: 0; top: 356px; height: 6px; background: var(--rule); }
  .back-foot { position: absolute; left: 0; right: 0; top: 380px; height: 8px; background: var(--rule); }
</style>
</head>
<body>
<main class="sheet">
  <section class="card card--front" aria-label="Card front">
    <div class="front-photo" role="img" aria-label="Photograph of a woman in soft grey tones"></div>
    <h1 class="front-brand">Marlow Thread</h1>
    <div class="front-strip"></div>
    <div class="front-band"></div>
  </section>

  <section class="card card--back" aria-label="Card back">
    <h2 class="back-name">Karen Whitfield</h2>
    <div class="back-panel">
      <div class="panel-rule"></div>
      <div class="panel-cut"></div>
      <p class="contact contact--web">
        <svg viewBox="0 0 16 16" fill="none" stroke="currentColor" stroke-width="1.6" stroke-linecap="round"><path d="M7 9.5 9.5 7"/><path d="M6 7.5 4.2 9.3a2.4 2.4 0 0 0 3.4 3.4L9.4 11"/><path d="M10 8.5l1.8-1.8a2.4 2.4 0 0 0-3.4-3.4L6.6 5"/></svg>
        www.marlowthread.example.au
      </p>
      <p class="contact contact--handle">
        <svg viewBox="0 0 16 16" fill="none" stroke="currentColor" stroke-width="1.6"><rect x="2" y="2" width="12" height="12"/></svg>
        _marlow_thread_
      </p>
      <p class="contact contact--phone">
        0498716204
        <svg viewBox="0 0 16 16" fill="currentColor"><path d="M4 1.5 6.3 4 5 5.8c.8 1.9 2.4 3.6 4.3 4.4L11 8.8l2.5 2.3-1.2 2.6C7 13.4 2.6 9 2.3 3z"/></svg>
      </p>
      <p class="contact contact--email">
        info@marlowthread.example.au
        <svg viewBox="0 0 16 16" fill="none" stroke="currentColor" stroke-width="1.4"><rect x="1.5" y="3.5" width="13" height="9"/><path d="M1.5 3.5 8 9l6.5-5.5"/></svg>
      </p>
    </div>
    <p class="back-social">www.fakebookexample.com/marlowthreadau/</p>
    <div class="back-rule"></div>
    <div class="back-foot"></div>
  </section>
</main>
</body>
</html>
```